Business card design for a dynamic IT consulting company

We need a business card design for a young firm, specialized in the Telecommunications/Consulting industry. The name of the company is Quindor and Partners Business Consulting Ltd. (Short name: Quindor and Partnes)
Quindor = solve read reverse, so we aim to be uncomplicated and solution-oriented. The small pipe in our logo is also related to the word solve. So we need a new business card design, which is simple, eye catching and something non traditional (I would probably prefer a square shaped design rather than a rectangle, but open for suggestions). Attached our logo.

Target Market(s)

Usually our customers are Tier1 Telecoms providers (Q-Netra, Palorix, etc) and their executives.

Industry/Entity Type

Business

Contact Information for Business Card

Name: Bence Tolnavari
Email: b.tolnavari@quindor.hu
Web: www.quindor.hu
Mobile: +36 30 518 2769
Title: Managing Director

Optional:
Company name: Quindor and Partners Ltd.
Address: 1087 Budapest, Tolvenka str. 28/C, Hungary

Font styles to use
Other font styles liked:
• helveticaneue_medium, Prime Regular are used now.

Colors

Designer to choose colors to be used in the design.

Requirements
Must have
• I would like to have a 2 sided design.
Nice to have
• I thought if we make the logo a bit bigger (without the company name), that could go to the back with the company name below. I though, if the pipe in the logo is somehow touchable on the business card, would be nice and unique.

```html
<!DOCTYPE html>
<html lang="en">
<head>
<meta charset="utf-8">
<title>Quindor and Partners – Business Card</title>
<link href="https://fonts.googleapis.com/css2?family=Arimo:wght@400;700&display=swap" rel="stylesheet">
<style>
  :root {
    --backdrop: #5a4a3b;
    --card: #f6f6f6;
    --ink: #555555;
    --blue: #1a97d5;
    --magenta: #b02b8c;
  }
  html, body {
    margin: 0;
    padding: 0;
    width: 1200px;
    height: 960px;
    overflow: hidden;
    background: var(--backdrop);
    font-family: "Arimo", Arial, sans-serif;
  }
  .stage {
    position: relative;
    width: 1200px;
    height: 960px;
  }
  .card {
    position: absolute;
    top: 309px;
    width: 342px;
    height: 343px;
    background: var(--card);
    box-shadow: 1px 2px 3px rgba(0,0,0,0.45);
    text-align: center;
    color: var(--ink);
  }
  .card--front { left: 235px; }
  .card--back { left: 623px; }

  .brand {
    display: inline-flex;
    align-items: center;
    gap: 7px;
    color: var(--ink);
    font-weight: 400;
  }
  .brand__dot {
    width: 9px;
    height: 9px;
    background: var(--magenta);
  }
  .card--front .brand {
    position: absolute;
    top: 388px;
    margin-top: -309px;
    left: 0;
    right: 0;
    justify-content: center;
    font-size: 26px;
  }
  .holder {
    position: absolute;
    top: 146px;
    left: 0;
    right: 0;
  }
  .holder__name {
    margin: 0;
    color: var(--blue);
    font-weight: 700;
    font-size: 19px;
    letter-spacing: 0.2px;
    line-height: 22px;
  }
  .holder__title {
    margin: 0;
    font-size: 15.5px;
    line-height: 18px;
    letter-spacing: 0.3px;
  }
  .contact {
    position: absolute;
    top: 198px;
    left: 0;
    right: 0;
    font-size: 14px;
    line-height: 18px;
    font-style: normal;
  }
  .contact p { margin: 0; }
  .contact__company { margin-top: 6px !important; }

  .card--back .brand {
    position: absolute;
    top: 188px;
    left: 0;
    right: 0;
    justify-content: center;
    font-size: 29px;
  }
</style>
</head>
<body>
<main class="stage">
  <section class="card card--front" aria-label="Card front">
    <div class="brand" style="top:79px;margin-top:0;"><span>Quindor</span><span class="brand__dot"></span></div>
    <div class="holder">
      <h1 class="holder__name">BENCE TOLNAVARI</h1>
      <p class="holder__title">MANAGING DIRECTOR</p>
    </div>
    <address class="contact">
      <p>+36 30 518 2769</p>
      <p>b.tolnavari@quindor.hu</p>
      <p class="contact__company">Quindor and Partners Ltd.,1087 Budapest</p>
      <p>Tolvenka str. 28/C, Hungary</p>
    </address>
  </section>

  <section class="card card--back" aria-label="Card back">
    <div class="brand"><span>Quindor &amp; Partners</span><span class="brand__dot"></span></div>
  </section>
</main>
</body>
</html>
```